Business Card Design Project

Looking for a logo and business card for a Real State Business i will be opening. The name is not choosen yet , but will probably be RWT IMOVEIS.
I was thinking black and silver colors, but am open to nice ideas.
I did add a business card that i liked a lot, am looking for something like that, with logo in black or silver in a black card. The logo i was thinking in the letters RWT as i uploaded or something or little and cute buildings or a house...just ideas, can be any nice logo.
Updates

You guys can add other colors if you want, I like colors very "BRIGHT" and "open", like red, pink, strong colors. almost glow in the dark colors. lol

Designers,

I've increased more 88 dollars in the budget for 1st place cause I will want envelope designs... small and big sizes.

So 1st place is now U$248,00. 

No need to send the envelope designs right now... only the business cards designs.

Thank you.

Industry/Entity Type

Business

Requirements
Must have
• Marcela Tavares Rocha

www.RWTimoveis-exemplo.com.br

+554187316042

marcela@rwtimoveis-exemplo.com.br

```html
<!DOCTYPE html>
<html lang="pt-BR">
<head>
<meta charset="utf-8">
<title>RWT Imoveis – Cartão de visita</title>
<link rel="stylesheet" href="https://fonts.googleapis.com/css2?family=Jost:wght@400&display=swap">
<style>
  :root {
    --backdrop: #3a3532;
    --card-black: #121212;
    --card-edge: #1c1c1c;
    --silver: #e6e6e6;
    --silver-soft: #bdbdbd;
    --gloss-black: #2e2e2e;
    --band-light: #d8d8d8;
    --band-dark: #1a1a1a;
  }
  html, body {
    margin: 0;
    padding: 0;
    width: 1200px;
    height: 716px;
    overflow: hidden;
    background: var(--backdrop);
  }
  .canvas {
    position: relative;
    width: 1200px;
    height: 716px;
    font-family: "Jost", sans-serif;
    font-weight: 400;
  }
  .card {
    position: absolute;
    top: 215px;
    width: 500px;
    height: 286px;
    background: var(--card-black);
    border: 1px solid var(--card-edge);
    box-sizing: border-box;
    overflow: hidden;
  }
  .card--front { left: 70px; }
  .card--back { left: 630px; }

  .brand {
    display: flex;
    align-items: center;
    gap: 10px;
    white-space: nowrap;
  }
  .brand__mark {
    width: 10px;
    height: 10px;
    flex: none;
  }
  .brand__name {
    letter-spacing: 0.5px;
  }
  .card--front .brand {
    position: absolute;
    left: 50%;
    top: 50%;
    transform: translate(-50%, -50%);
  }
  .card--front .brand__name {
    font-size: 40px;
    color: var(--gloss-black);
  }
  .card--front .brand__mark { background: var(--gloss-black); }

  .mosaic-band {
    position: absolute;
    top: 0;
    height: 100%;
  }
  .mosaic-band--left {
    left: 40px;
    width: 44px;
    background: linear-gradient(180deg, var(--band-light) 0%, #6a6a6a 40%, var(--band-dark) 75%, #3a3a3a 100%);
  }
  .mosaic-band--right {
    right: 50px;
    width: 48px;
    background: linear-gradient(180deg, #3a3a3a 0%, var(--band-light) 25%, #7a7a7a 55%, var(--band-dark) 100%);
  }

  .contact-side {
    position: absolute;
    left: 84px;
    right: 98px;
    top: 0;
    bottom: 0;
    display: flex;
    flex-direction: column;
    align-items: center;
    justify-content: center;
  }
  .card--back .brand__name {
    font-size: 26px;
    color: var(--silver);
  }
  .card--back .brand__mark { background: var(--silver); }
  .holder-name {
    margin: 16px 0 10px;
    font-size: 13px;
    letter-spacing: 1.5px;
    color: var(--silver);
  }
  .contact-list {
    list-style: none;
    margin: 0;
    padding: 0;
    font-size: 10px;
    letter-spacing: 0.8px;
    line-height: 1.7;
    color: var(--silver-soft);
    text-align: left;
  }
</style>
</head>
<body>
<main class="canvas">
  <section class="card card--front" aria-label="Frente do cartão">
    <div class="brand">
      <span class="brand__mark"></span>
      <span class="brand__name">RWT IMOVEIS</span>
    </div>
  </section>

  <section class="card card--back" aria-label="Verso do cartão">
    <div class="mosaic-band mosaic-band--left" role="img" aria-label="Faixa decorativa em mosaico prateado"></div>
    <div class="mosaic-band mosaic-band--right" role="img" aria-label="Faixa decorativa em mosaico prateado"></div>
    <div class="contact-side">
      <div class="brand">
        <span class="brand__mark"></span>
        <span class="brand__name">RWT IMOVEIS</span>
      </div>
      <p class="holder-name">Marcela Tavares Rocha</p>
      <ul class="contact-list">
        <li>+554187316042</li>
        <li>marcela@rwtimoveis-exemplo.com.br</li>
        <li>www.RWTimoveis-exemplo.com.br</li>
      </ul>
    </div>
  </section>
</main>
</body>
</html>
```